Emergency and Referral Vet Hospital promotional sticker design

We're looking at getting some stickers designed that we could give to clients to put on their cars for promotion and advertising. If they could also be suitable for a goodie bag for conference too that would be great. I like the look of water-colour backgrounds, we'll need to include our logo and probably our address (Unit 3/215 Korrinup Road Tallowmere). We also have a hospital motto "... because they're family" if that could somehow be integrated, we only care for small animals (dogs, cats etc) but the design is very open to suggestion. Would love to see what you can create.

Industry/Entity Type

Veterinary

Colors
0054AA
0677BA
7BADD7
CADEEF
E8F1F8
0094D4
00A9DD
6FCCEA
C7EBF8
E9F6FB

Requirements
Nice to have
• Think beach vibes, blues maybe paw print shapes etc

```html
<!DOCTYPE html>
<html lang="en">
<head>
<meta charset="UTF-8">
<title>Tides Vet Hospital – Sticker Designs</title>
<link rel="stylesheet" href="https://fonts.googleapis.com/css2?family=Kaushan+Script&family=Nunito:wght@700;800&display=swap">
<style>
  :root {
    --page: #ffffff;
    --card: #f7f8fd;
    --navy: #0d3d66;
    --ink: #111418;
    --cross: #a9c6f0;
    --wash-core: #3fd3ea;
    --wash-mid: #7fc4f0;
    --wash-soft: #a9c2f2;
    --wash-edge: #e9f1fb;
  }
  * { margin: 0; padding: 0; box-sizing: border-box; }
  html, body {
    width: 1000px; height: 1200px; overflow: hidden;
    background: var(--page);
  }
  .canvas { position: relative; width: 1000px; height: 1200px; }

  .wash-layer { position: absolute; left: 0; top: 0; width: 1000px; height: 1200px; }

  .rect-sticker {
    position: absolute; left: 183px; top: 610px; width: 658px; height: 542px;
    background: var(--card);
    box-shadow: 0 12px 30px rgba(0,0,0,0.22);
  }

  .motto {
    position: absolute; left: 0; width: 1000px; text-align: center;
    font-family: "Kaushan Script", cursive;
    color: var(--navy); white-space: nowrap;
  }
  .brand-name {
    position: absolute; left: 0; width: 1000px; text-align: center;
    font-family: "Nunito", sans-serif; font-weight: 800;
    color: var(--ink); letter-spacing: 0.5px;
  }
  .address {
    position: absolute; left: 0; width: 1000px; text-align: center;
    font-family: "Nunito", sans-serif; font-weight: 700;
    color: var(--ink); font-size: 13px; line-height: 18px;
  }

  .diecut .motto { top: 250px; font-size: 44px; left: -10px; }
  .diecut .brand-name { top: 425px; font-size: 40px; left: 16px; }
  .diecut .address { top: 474px; left: 16px; }

  .rectangle .motto { top: 833px; font-size: 46px; left: 30px; }
  .rectangle .brand-name { top: 1022px; font-size: 40px; left: 28px; }
  .rectangle .address { top: 1066px; left: 28px; }
</style>
</head>
<body>
<div class="canvas">

  <div class="rect-sticker"></div>

  <svg class="wash-layer" viewBox="0 0 1000 1200" role="img" aria-label="Soft blue and turquoise watercolour wash with scattered white paw prints">
    <defs>
      <radialGradient id="wash" cx="0.38" cy="0.52" r="0.62">
        <stop offset="0" stop-color="var(--wash-core)"/>
        <stop offset="0.35" stop-color="var(--wash-mid)"/>
        <stop offset="0.7" stop-color="var(--wash-soft)"/>
        <stop offset="1" stop-color="var(--wash-edge)"/>
      </radialGradient>
      <filter id="lift" x="-10%" y="-10%" width="120%" height="130%">
        <feDropShadow dx="0" dy="8" stdDeviation="10" flood-color="#000" flood-opacity="0.14"/>
      </filter>
      <path id="blob" d="M205 378 C190 330 240 290 230 250 C220 190 300 180 300 120 C330 70 420 60 470 40 C560 30 620 70 690 90 C760 110 800 190 815 240 C825 290 790 330 770 360 C760 410 730 450 670 470 C600 500 560 540 470 555 C400 565 330 520 300 470 C260 440 210 420 205 378 Z"/>
    </defs>

    <g class="diecut-wash" filter="url(#lift)">
      <use href="#blob" fill="#ffffff" stroke="#ffffff" stroke-width="18" stroke-linejoin="round"/>
      <use href="#blob" fill="url(#wash)" opacity="0.85"/>
    </g>

    <g class="rect-wash" transform="translate(12 585)">
      <use href="#blob" fill="url(#wash)" opacity="0.85"/>
    </g>

    <path class="care-cross" d="M622 308 h44 a6 6 0 0 1 6 6 v38 h38 a6 6 0 0 1 6 6 v36 a6 6 0 0 1 -6 6 h-38 v38 a6 6 0 0 1 -6 6 h-44 a6 6 0 0 1 -6 -6 v-38 h-20 a6 6 0 0 1 -6 -6 v-36 a6 6 0 0 1 6 -6 h20 v-38 a6 6 0 0 1 6 -6 Z"
          fill="none" stroke="var(--cross)" stroke-width="2.5"/>
    <path class="care-cross" d="M637 893 h46 a6 6 0 0 1 6 6 v40 h40 a6 6 0 0 1 6 6 v38 a6 6 0 0 1 -6 6 h-40 v40 a6 6 0 0 1 -6 6 h-46 a6 6 0 0 1 -6 -6 v-40 h-20 a6 6 0 0 1 -6 -6 v-38 a6 6 0 0 1 6 -6 h20 v-40 a6 6 0 0 1 6 -6 Z"
          fill="none" stroke="var(--cross)" stroke-width="2.5"/>
  </svg>

  <div class="diecut">
    <p class="motto">… because they’re family</p>
    <p class="brand-name">Tides</p>
    <p class="address">Unit 3<br>215 Korrinup Road Tallowmere</p>
  </div>

  <div class="rectangle">
    <p class="motto">… because they’re family</p>
    <p class="brand-name">Tides</p>
    <p class="address">Unit 3<br>215 Korrinup Road Tallowmere</p>
  </div>

</div>
</body>
</html>
```